BUSINESS CARD DESIGN

NAME- DALE VORSKIN
PHONE NUMER - 555- 714-9082
EMAIL- OFFICE@TRV-GROUNDMAKRZ.COM
BACK OF CARD- SPEACIALIZES IN LAND CLEARING, FORESTRY MUCLHING AND EXCAVATION

Contact Information for Business Card

NAME- DALE VORSKIN PHONE NUMER - 555- 714-9082 EMAIL- OFFICE@TRV-GROUNDMAKRZ.COM BACK OF CARD- SPEACIALIZES IN LAND CLEARING , MUCLHING AND EXCAVATION

```html
<!DOCTYPE html>
<html lang="en">
<head>
<meta charset="utf-8">
<title>Trevant Groundmakrz – Business Card</title>
<link href="https://fonts.googleapis.com/css2?family=Montserrat:wght@600;700&display=swap" rel="stylesheet">
<style>
  :root {
    --gold: #f8b518;
    --paper: #ffffff;
    --backdrop: #efefef;
  }
  * { margin: 0; padding: 0; box-sizing: border-box; }
  html, body { width: 1200px; height: 1131px; overflow: hidden; background: var(--backdrop); }
  body { position: relative; font-family: "Montserrat", sans-serif; }

  .card { position: absolute; left: 240px; width: 688px; height: 394px; overflow: hidden; }
  .card-front { top: 152px; background: var(--paper); }
  .card-back { top: 627px; background: var(--gold); }

  .brand { position: absolute; display: flex; flex-direction: column; align-items: center; font-weight: 700; text-align: center; white-space: nowrap; }
  .brand-mark { border-radius: 50%; }
  .brand-name, .brand-region, .brand-phone { display: block; line-height: 1.2; }

  .card-front .brand { left: 36px; top: 112px; width: 240px; color: var(--gold); }
  .card-front .brand-mark { width: 92px; height: 92px; background: var(--gold); }
  .card-front .brand-name { margin-top: 16px; font-size: 13px; letter-spacing: 0.5px; }
  .card-front .brand-region { margin-top: 2px; font-size: 11px; letter-spacing: 4px; }
  .card-front .brand-phone { margin-top: 2px; font-size: 10px; letter-spacing: 5px; }

  .card-back .brand { left: 184px; top: 70px; width: 320px; color: var(--paper); }
  .card-back .brand-mark { width: 132px; height: 132px; background: var(--paper); }
  .card-back .brand-name { margin-top: 18px; font-size: 18px; letter-spacing: 0.8px; }
  .card-back .brand-region { margin-top: 3px; font-size: 14px; letter-spacing: 6px; }
  .card-back .brand-phone { margin-top: 3px; font-size: 12px; letter-spacing: 8px; }

  .divider { position: absolute; left: 321px; top: 100px; width: 3px; height: 220px; background: var(--gold); }

  .person { position: absolute; left: 374px; top: 92px; color: var(--gold); }
  .person-name { font-size: 32px; font-weight: 600; line-height: 1; letter-spacing: 0.3px; }
  .person-role { display: inline-block; margin-top: 8px; font-size: 23px; font-weight: 600; line-height: 1; padding-bottom: 3px; border-bottom: 3px solid var(--gold); }

  .contacts { position: absolute; left: 373px; top: 214px; list-style: none; }
  .contact { display: flex; align-items: center; height: 20px; margin-bottom: 20px; color: var(--gold); font-size: 16px; font-weight: 700; white-space: nowrap; }
  .contact svg { width: 26px; height: 22px; margin-right: 16px; flex: none; }

  .tagline { position: absolute; left: 0; right: 0; top: 346px; text-align: center; color: var(--paper); font-size: 13px; font-weight: 700; letter-spacing: 0.8px; white-space: nowrap; }
</style>
</head>
<body>
  <section class="card card-front">
    <div class="brand">
      <span class="brand-mark"></span>
      <span class="brand-name">TREVANT GROUNDMAKRZ LLC</span>
      <span class="brand-region">HAWAII</span>
      <span class="brand-phone">555-714-9082</span>
    </div>
    <div class="divider"></div>
    <div class="person">
      <h1 class="person-name">DALE VORSKIN</h1>
      <p class="person-role">OWNER</p>
    </div>
    <ul class="contacts">
      <li class="contact">
        <svg viewBox="0 0 26 22" fill="none" stroke="currentColor" stroke-width="2"><rect x="2" y="4" width="22" height="14" fill="currentColor"/><path d="M2 4l11 9 11-9M2 18l8-7M24 18l-8-7" stroke="#fff" stroke-width="1.6"/></svg>
        @TRV-GROUNDMAKRZ.COM
      </li>
      <li class="contact">
        <svg viewBox="0 0 26 22" fill="none" stroke="currentColor" stroke-width="1.6" stroke-linecap="round"><path d="M5 3l4 0 2 5-3 2c1.5 3 3.5 5 6.5 6.5l2-3 5 2v4c-9 1-17-7-16.5-16.5z"/><path d="M15 3a6 6 0 0 1 5 5M15 6a3 3 0 0 1 2 2"/></svg>
        +555- 714-9082
      </li>
      <li class="contact">
        <svg viewBox="0 0 26 22" fill="none" stroke="currentColor" stroke-width="1.5"><circle cx="13" cy="11" r="9.5"/><ellipse cx="13" cy="11" rx="4.5" ry="9.5"/><path d="M3.5 11h19M5 6h16M5 16h16M13 1.5v19"/></svg>
        www.trv-groundmakrz.com
      </li>
    </ul>
  </section>

  <section class="card card-back">
    <div class="brand">
      <span class="brand-mark"></span>
      <span class="brand-name">TREVANT GROUNDMAKRZ LLC</span>
      <span class="brand-region">HAWAII</span>
      <span class="brand-phone">555-714-9082</span>
    </div>
    <p class="tagline">SPEACIALIZES IN LAND CLEARING , MUCLHING AND EXCAVATION</p>
  </section>
</body>
</html>
```